Local fast-growing company in the service sector

We are looking for a modern business card design, which should also appear on our letterheads

Target Market(s)

Private and industrial sectors

Contact Information for Business Card

Vorname Name
Kellberger Str. 18
73614 Schorndorf
Tel.: 07146-839214-0
Name@agentur-kvtl.de

Colors
9d9d9d
919191
aaaaaa

Requirements
Must have
• The logo (file) in silver

```html
<!DOCTYPE html>
<html lang="de">
<head>
<meta charset="utf-8">
<title>KVTL – Visitenkarte</title>
<link rel="stylesheet" href="https://fonts.googleapis.com/css2?family=Arimo:wght@400;700&display=swap">
<style>
  :root {
    --page-bg: #dedcd8;
    --card-top: #f1f2f2;
    --card-bottom: #e3e5e6;
    --card-edge: #c9cbcc;
    --silver: #9d9d9d;
    --silver-dark: #6f6f6f;
    --band: #2f2f31;
    --band-deep: #242426;
    --stripe: #333335;
    --band-text: #e4e4e4;
    --band-muted: #aaaaaa;
    --address: #3a3a3c;
  }
  * { margin: 0; padding: 0; box-sizing: border-box; }
  html, body {
    width: 1200px;
    height: 970px;
    overflow: hidden;
    background: var(--page-bg);
    font-family: "Arimo", Arial, sans-serif;
  }
  .business-card {
    position: absolute;
    left: 100px;
    top: 185px;
    width: 1000px;
    height: 600px;
    background: linear-gradient(180deg, var(--card-top), var(--card-bottom));
    border: 1px solid var(--card-edge);
    box-shadow: 0 18px 40px rgba(0,0,0,0.18);
    overflow: hidden;
  }
  .brand {
    position: absolute;
    left: 250px;
    top: 88px;
    display: flex;
    align-items: center;
    gap: 28px;
  }
  .brand-mark {
    width: 110px;
    height: 110px;
    background: var(--silver);
  }
  .brand-text { display: flex; flex-direction: column; }
  .brand-name {
    font-size: 96px;
    font-weight: 700;
    line-height: 0.95;
    color: var(--silver-dark);
    letter-spacing: 2px;
  }
  .brand-web {
    font-size: 30px;
    font-weight: 700;
    color: var(--silver-dark);
    letter-spacing: 1px;
    margin-top: 2px;
  }
  .stripe {
    position: absolute;
    left: 0;
    width: 100%;
    background: var(--stripe);
  }
  .stripe-a { top: 310px; height: 6px; }
  .stripe-b { top: 320px; height: 3px; }
  .stripe-c { top: 328px; height: 5px; }
  .stripe-d { top: 518px; height: 5px; }
  .stripe-e { top: 528px; height: 3px; }
  .stripe-f { top: 536px; height: 8px; }
  .contact-band {
    position: absolute;
    left: 0;
    top: 340px;
    width: 100%;
    height: 174px;
    background: linear-gradient(180deg, var(--band), var(--band-deep));
  }
  .person {
    position: absolute;
    left: 84px;
    top: 54px;
    width: 300px;
    text-align: center;
    white-space: nowrap;
  }
  .person-name {
    font-size: 30px;
    font-weight: 700;
    color: var(--band-text);
    letter-spacing: 0.5px;
    line-height: 1.2;
  }
  .person-role {
    font-size: 23px;
    color: var(--band-text);
    margin-top: 2px;
  }
  .band-divider {
    position: absolute;
    left: 496px;
    top: 36px;
    width: 2px;
    height: 100px;
    background: linear-gradient(180deg, transparent, var(--band-muted), transparent);
  }
  .contact-list {
    position: absolute;
    left: 598px;
    top: 56px;
    list-style: none;
  }
  .contact-list li {
    display: flex;
    align-items: center;
    gap: 18px;
    font-size: 23px;
    color: var(--band-muted);
    letter-spacing: 1.5px;
    height: 34px;
    white-space: nowrap;
  }
  .contact-icon { width: 24px; height: 24px; flex: none; }
  .address {
    position: absolute;
    left: 0;
    top: 562px;
    width: 100%;
    text-align: center;
    font-size: 22px;
    letter-spacing: 2.5px;
    color: var(--address);
    text-transform: uppercase;
    white-space: nowrap;
  }
</style>
</head>
<body>
  <div class="business-card">
    <div class="brand">
      <div class="brand-mark"></div>
      <div class="brand-text">
        <span class="brand-name">KVTL</span>
        <span class="brand-web">agentur-kvtl.de</span>
      </div>
    </div>

    <div class="stripe stripe-a"></div>
    <div class="stripe stripe-b"></div>
    <div class="stripe stripe-c"></div>

    <div class="contact-band">
      <div class="person">
        <div class="person-name">JONAS WEBER</div>
        <div class="person-role">Director</div>
      </div>
      <div class="band-divider"></div>
      <ul class="contact-list">
        <li>
          <svg class="contact-icon" viewBox="0 0 24 24" aria-hidden="true">
            <circle cx="12" cy="12" r="12" fill="#aaaaaa"/>
            <path d="M6 10c0-2 2-3 6-3s6 1 6 3l-2 1-1-2h-6l-1 2z M8 12h8l1 5H7z" fill="#2f2f31"/>
          </svg>
          <span>07146-839214-0</span>
        </li>
        <li>
          <svg class="contact-icon" viewBox="0 0 24 24" aria-hidden="true">
            <circle cx="12" cy="12" r="12" fill="#aaaaaa"/>
            <rect x="6" y="8" width="12" height="8" fill="none" stroke="#2f2f31" stroke-width="1.6"/>
            <path d="M6 8l6 5 6-5" fill="none" stroke="#2f2f31" stroke-width="1.6"/>
          </svg>
          <span>Name@agentur-kvtl.de</span>
        </li>
      </ul>
    </div>

    <div class="stripe stripe-d"></div>
    <div class="stripe stripe-e"></div>
    <div class="stripe stripe-f"></div>

    <p class="address">Kellberger Str. 18, 73614 Schorndorf</p>
  </div>
</body>
</html>
```